Dental Implant Logo and Business Card for Local Dentist

Design a unique business card and a logo that incorporates a dental implant as a primary focal point or a part of the text. New logo design & business card needs to incorporate our businesses old star shaped logo (attached) and a dental implant, along with our business name. Star logo does not have to remain the exact same colors and can be any size. Looking for a warm, friendly (non-aggressive) design that uses colors in the blue-green palate, partial to mint-turquoise color similar to the images attached . SIMPLE IS GOOD, but looking for creativity to bring all the elements together. OK to incorporate a splash of color. I have attached a few images of implant logos I like along with our existing star shaped logo. *I have also uploaded some images that represent local landscapes & images for the back of the business card. I would like to include a silhouette or sketch that represents one one of these areas on the back of the business card to convey the connection to our community and local roots of our business since we are 4th generation members of this community . Can visit our dental practice website for more info. www.hartwellandodegarddentalcare.example Card Must Haves on Front of Card:1. business name "Hartwell & Odegard Dental Care" 2. My Name: "Colin Odegard D.D.S."3. Phone # (925) 754-6020Other info for card (can be front or back)Address: 7840 Quarry Ridge Rd. #2C Brookhollow, Ca 94531e-mail: millerandsimarrodentalcare@gmail.comcosmetic, family, & impDesign a unique business card and a logo that incorporates a dental implant as a primary focal point or a part of the text. New logo design & business card needs to incorporate our businesses old star shaped logo (attached) and a dental implant, along with our business name. Star logo does not have to remain the exact same colors and can be any size. Looking for a warm, friendly (non-aggressive) design that uses colors in the blue-green palate, partial to mint-turquoise color similar to the images attached . SIMPLE IS GOOD, but looking for creativity to bring all the elements together. OK to incorporate a splash of color. I have attached a few images of implant logos I like along with our existing star shaped logo. *I have also uploaded some images that represent local landscapes & images for the back of the business card. I would like to include a silhouette or sketch that represents one one of these areas on the back of the business card to convey the connection to our community and local roots of our business since we are 4th generation members of this community . Can visit our dental practice website for more info. www.hartwellandodegarddentalcare.example Card Must Haves on Front of Card:1. business name "Hartwell & Odegard Dental Care" 2. My Name: "Colin Odegard D.D.S."3. Phone # (925) 754-6020Other info for card (can be front or back)Address: 7840 Quarry Ridge Rd. #2C Brookhollow, Ca 94531e-mail: millerandsimarrodentalcare@gmail.comcosmetic, family, & implant dentistry

Target Market(s)

Families

Industry/Entity Type

Dental

Contact Information for Business Card

See Project description above

Logo Text

Hartwell & Odegard Dental Care

Font styles to use
Serif

Colors
ffffff
33b8a4
87cfc6
0492cd
33a6d7
0255a3

Requirements
Must have
• *See Description...
• Card Must Haves on Front of Card:
• 1. business name "Hartwell & Odegard Dental Care"
• 2. My Name: "Colin Odegard D.D.S."
• 3. Phone # (555) 318-4297
• Other info for card (can be front or back)
• Address: 7840 Quarry Ridge Rd. #2C Brookhollow, Ca 90217
• e-mail: hartwellandodegarddentalcare@example-mail.com
Nice to have
• Local image sketch or silhouette on back side of business card with remaining information on back: address, website, e-mail etc.

```html
<!DOCTYPE html>
<html lang="en">
<head>
<meta charset="utf-8">
<title>Hartwell &amp; Odegard Dental Care – Business Card</title>
<link href="https://fonts.googleapis.com/css2?family=Jost:wght@300;400;500&display=swap" rel="stylesheet">
<style>
  :root {
    --page: #ececec;
    --paper: #ffffff;
    --sky: #33a6d7;
    --teal: #1db39f;
    --mint: #87cfc6;
    --brand-blue: #1f6fc0;
    --ink: #1e2a2a;
    --tools: #d9dcde;
  }
  * { box-sizing: border-box; margin: 0; padding: 0; }
  html, body { width: 1200px; height: 800px; overflow: hidden; }
  body {
    background: var(--page);
    font-family: "Jost", sans-serif;
    position: relative;
  }
  .card {
    position: absolute;
    top: 245px;
    width: 540px;
    height: 309px;
    background: var(--paper);
    overflow: hidden;
    box-shadow: 0 2px 8px rgba(0,0,0,0.12);
  }
  .card--front { left: 40px; }
  .card--back { left: 620px; }
  .card__shapes { position: absolute; inset: 0; width: 100%; height: 100%; }

  .brand {
    position: absolute;
    left: 0; right: 0; top: 92px;
    text-align: center;
    color: var(--brand-blue);
    font-weight: 300;
  }
  .brand__mark {
    display: block;
    width: 40px; height: 40px;
    margin: 0 auto 12px;
    border: 2px solid var(--brand-blue);
    border-radius: 50%;
  }
  .brand__name { font-size: 30px; line-height: 1.05; letter-spacing: 0.5px; }

  .dentist {
    position: absolute;
    left: 30px; top: 20px;
    color: var(--ink);
    font-weight: 500;
    font-size: 17px;
    line-height: 1.1;
    padding-bottom: 3px;
    border-bottom: 1.5px solid var(--ink);
    width: 175px;
  }
  .tools-art {
    position: absolute;
    left: 38px; top: 112px;
    width: 118px; height: 78px;
    background: linear-gradient(135deg, #eef0f1, var(--tools));
  }
  .contact {
    position: absolute;
    right: 0; top: 168px;
    list-style: none;
    display: flex; flex-direction: column; gap: 9px;
    align-items: flex-end;
  }
  .contact__item {
    display: flex; align-items: center; gap: 8px;
    background: var(--paper);
    color: var(--ink);
    font-size: 9.5px;
    padding: 3px 10px 3px 10px;
    min-width: 250px;
    justify-content: flex-end;
  }
  .contact__icon { width: 11px; height: 11px; flex: none; }
</style>
</head>
<body>

<section class="card card--front" aria-label="Card front">
  <svg class="card__shapes" viewBox="0 0 540 309" aria-hidden="true">
    <polygon points="0,92 96,0 238,62" fill="var(--sky)"/>
    <polygon points="0,180 100,148 168,309 0,309" fill="var(--teal)"/>
    <polygon points="392,168 540,98 540,300" fill="var(--mint)"/>
  </svg>
  <div class="brand">
    <span class="brand__mark"></span>
    <p class="brand__name">Hartwell &amp; Odegard<br>Dental Care</p>
  </div>
</section>

<section class="card card--back" aria-label="Card back">
  <svg class="card__shapes" viewBox="0 0 540 309" aria-hidden="true">
    <polygon points="0,0 115,0 300,108 0,86" fill="var(--mint)"/>
    <polygon points="205,125 540,152 540,309 300,309" fill="var(--teal)"/>
  </svg>
  <p class="dentist">Colin Odegard<br>D.D.S.</p>
  <div class="tools-art" role="img" aria-label="Sketch of dental instruments"></div>
  <ul class="contact">
    <li class="contact__item">Address: 7840 Quarry Ridge Rd. #2C, Brookhollow, Ca 90217
      <svg class="contact__icon" viewBox="0 0 12 12"><path d="M6 1a3.5 3.5 0 0 1 3.5 3.5C9.5 7 6 11 6 11S2.5 7 2.5 4.5A3.5 3.5 0 0 1 6 1z" fill="var(--ink)"/><circle cx="6" cy="4.5" r="1.2" fill="#fff"/></svg>
    </li>
    <li class="contact__item">www.hartwellandodegarddentalcare.example
      <svg class="contact__icon" viewBox="0 0 12 12"><circle cx="6" cy="6" r="5" fill="none" stroke="var(--ink)"/><path d="M1 6h10M6 1c-2 2-2 8 0 10M6 1c2 2 2 8 0 10" fill="none" stroke="var(--ink)" stroke-width="0.8"/></svg>
    </li>
    <li class="contact__item">hartwellandodegarddentalcare@example-mail.com
      <svg class="contact__icon" viewBox="0 0 12 12"><rect x="1" y="2.5" width="10" height="7" fill="var(--ink)"/><path d="M1 2.5l5 4 5-4" fill="none" stroke="#fff" stroke-width="0.9"/></svg>
    </li>
    <li class="contact__item">(555) 318-4297
      <svg class="contact__icon" viewBox="0 0 12 12"><rect x="3" y="0.5" width="6" height="11" rx="1" fill="var(--ink)"/><rect x="4" y="2" width="4" height="7" fill="#fff"/></svg>
    </li>
  </ul>
</section>

</body>
</html>
```